High-End Print/Digital Ad for Unique Luxury Travel Company Required

Objective:
Design a compelling and visually striking advertisement that highlights our company’s unmatched luxury travel experiences. The ad should elevate our brand image, spark curiosity, and drive prospective clients to contact us.
Target Audience:
• Affluent individuals seeking extraordinary, tailor-made travel experiences
• Affluent, luxury, high-net-worth individuals looking for value, expertise, and white-glove service
• Professionals or retirees who appreciate unique, thoughtfully curated travel over mainstream tourism
Key Messages to Communicate:
• One-of-a-kind luxury travel: Once-in-a-lifetime experiences that are curated with creativity and meticulous attention to detail
• Exceptional service: White-glove, personalized planning from start to finish
• 38 years’ travel experience – expert knowledge of destinations, modes of travel, premium accommodations and well-established, meaningful industry connections.
• Highly trusted: Cruise line executives often say, “No one does what you do.”
Tone and Style:
• Elegant, luxurious, sophisticated
• Eye-catching, polished, and modern
• Professional but warm—conveys trust and credibility
• High-impact visuals (full-bleed imagery, custom graphics, or high-end photography)
Deliverables:
• One full-page print ad and digital ad
• Ready-to-print, high-resolution file + working file (PSD, AI, etc.)
Optional: Social media-optimized version or short motion-graphic variation (if designer offers it)
Inspiration & Visual Style Suggestions:
• Think Lumen Voyages, Harrow Pike Wanderer, Silver Quill, or Orvel Retreats ad styles
• Large, emotive imagery with elegant typography
• Clean layout that speaks luxury, clarity, and trust
Copy Direction (draft):
For those who’ve explored the world—and crave something beyond the ordinary.
Each journey is a masterfully curated experience, rich in detail, seamless in execution, and unforgettable in every way.
Founded in 1997, Tidewell Journeys is a unique travel company specializing in cruising, all-inclusive luxury properties, and tours world-wide for individuals, groups, and incentives.
We offer an exceptional range of services designed to ensure every journey is flawlessly executed and truly unforgettable.
Let us help you plan your next extraordinary adventure.
Note: You may refine the copy slightly based on layout or format needs.
Other Resources for References:
1. Website - www.tidewelljourneys-example.com

```html
<!DOCTYPE html>
<html lang="en">
<head>
<meta charset="utf-8">
<title>Tidewell Journeys – Luxury Reimagined</title>
<link rel="stylesheet" href="https://fonts.googleapis.com/css2?family=Playfair+Display:wght@400;700&family=Poppins:wght@400;600;700&display=swap">
<style>
  :root {
    --ink: #1a0f0a;
    --white: #ffffff;
    --cream: #fbeee0;
    --gold: #f5a52a;
    --rock-deep: #5a2310;
    --rock: #a8461c;
    --rock-light: #d9742f;
    --glow: #fff6e6;
  }
  * { margin: 0; padding: 0; box-sizing: border-box; }
  html, body { width: 981px; height: 1200px; overflow: hidden; background: var(--ink); }
  .ad {
    position: relative;
    width: 981px;
    height: 1200px;
    overflow: hidden;
    font-family: "Poppins", sans-serif;
    color: var(--white);
  }
  .hero-photo {
    position: absolute; inset: 0;
    background:
      radial-gradient(ellipse 140px 120px at 620px 900px, var(--glow) 0%, rgba(255,240,210,0.85) 35%, rgba(255,200,120,0) 100%),
      radial-gradient(ellipse 170px 260px at 640px 760px, rgba(250,246,240,0.95) 0%, rgba(250,240,225,0.7) 45%, rgba(230,140,60,0) 100%),
      radial-gradient(ellipse 260px 200px at 560px 620px, rgba(255,200,120,0.75) 0%, rgba(230,130,50,0) 100%),
      radial-gradient(ellipse 220px 360px at 440px 250px, rgba(200,198,196,0.9) 0%, rgba(185,182,179,0.5) 50%, rgba(185,182,179,0) 100%),
      linear-gradient(180deg, #121212 0%, #3a3634 8%, rgba(120,60,30,0) 22%),
      linear-gradient(100deg, var(--rock-deep) 0%, var(--rock) 25%, var(--rock-light) 45%, var(--rock) 70%, var(--rock-deep) 100%);
  }
  .hero-shade {
    position: absolute; inset: 0;
    background: linear-gradient(180deg, rgba(0,0,0,0) 70%, rgba(40,18,8,0.75) 88%, rgba(25,12,6,0.92) 100%);
  }
  .headline {
    position: absolute; left: 70px; top: 19px;
    font-family: "Playfair Display", serif;
    font-weight: 700;
    font-size: 235px;
    line-height: 1;
    letter-spacing: -4px;
    color: var(--white);
  }
  .headline-accent {
    position: absolute; left: 72px; top: 248px;
    font-family: "Playfair Display", serif;
    font-weight: 700;
    font-size: 106px;
    line-height: 1;
    letter-spacing: -1px;
    color: var(--gold);
  }
  .tagline {
    position: absolute; left: 73px; top: 364px;
    font-family: "Playfair Display", serif;
    font-weight: 400;
    font-size: 43px;
    line-height: 44px;
    color: var(--cream);
    white-space: nowrap;
  }
  .feature { position: absolute; left: 72px; width: 320px; }
  .feature-bespoke { top: 500px; }
  .feature-service { top: 600px; }
  .feature-reputation { top: 696px; }
  .feature-title { font-weight: 600; font-size: 21px; line-height: 26px; }
  .feature-text { font-size: 15.5px; line-height: 19px; margin-top: 2px; white-space: nowrap; }
  .feature-quote { font-weight: 600; font-size: 17px; line-height: 22px; margin-top: 6px; white-space: nowrap; }
  .feature-source { font-size: 15.5px; line-height: 19px; }
  .badge {
    position: absolute; left: 612px; top: 594px;
    width: 178px; height: 178px; border-radius: 50%;
    background: var(--gold);
    display: flex; flex-direction: column; align-items: center; justify-content: center;
    text-align: center; padding: 0 20px;
  }
  .badge-title { color: var(--ink); font-weight: 600; font-size: 15px; line-height: 16px; }
  .badge-text { color: var(--white); font-size: 10.5px; line-height: 13.5px; margin-top: 8px; }
  .contact { position: absolute; left: 72px; top: 1034px; }
  .contact-cta { color: var(--gold); font-weight: 700; font-size: 20px; line-height: 26px; white-space: nowrap; }
  .contact-line { display: flex; align-items: center; gap: 9px; font-weight: 600; white-space: nowrap; }
  .contact-phone { font-size: 31px; margin-top: 6px; line-height: 38px; }
  .contact-web { font-size: 23px; margin-top: 0; line-height: 32px; }
  .contact-line svg { flex: none; }
  .brand {
    position: absolute; right: 74px; top: 1094px;
    display: flex; align-items: center; gap: 8px;
    font-family: "Playfair Display", serif;
    font-weight: 400; font-size: 22px; letter-spacing: 1px;
    color: var(--white); text-transform: uppercase;
  }
  .brand-dot { width: 30px; height: 30px; border-radius: 50%; background: var(--white); }
</style>
</head>
<body>
<main class="ad">
  <div class="hero-photo" role="img" aria-label="Sunlit red sandstone double arch in a desert, with a small lone traveler silhouetted against a bright sunburst beneath the arch and patches of snow on the rocks"></div>
  <div class="hero-shade"></div>

  <h1 class="headline">Luxury</h1>
  <p class="headline-accent">REIMAGINED</p>
  <p class="tagline">Once-in-a-lifetime journeys, designed<br>with vision, trust, and timeless detail.</p>

  <section class="features">
    <div class="feature feature-bespoke">
      <h2 class="feature-title">Bespoke Experiences</h2>
      <p class="feature-text">Impeccably curated adventures<br>crafted with creativity and care.</p>
    </div>
    <div class="feature feature-service">
      <h2 class="feature-title">White-Glove Service</h2>
      <p class="feature-text">From first idea to final return, every<br>detail is flawlessly handled.</p>
    </div>
    <div class="feature feature-reputation">
      <h2 class="feature-title">Unrivaled Reputation</h2>
      <p class="feature-quote">"No one does what you do."</p>
      <p class="feature-source">Cruise Line Executive</p>
    </div>
  </section>

  <aside class="badge">
    <p class="badge-title">EXPERTISE<br>YOU CAN<br>TRUST</p>
    <p class="badge-text">38 years of unmatched insight, global connections, and premium access.</p>
  </aside>

  <footer class="contact">
    <p class="contact-cta">Let us create your next unforgettable escape</p>
    <p class="contact-line contact-phone">
      <svg width="18" height="18" viewBox="0 0 18 18" aria-hidden="true">
        <circle cx="9" cy="9" r="9" fill="var(--gold)"/>
        <path d="M6 4.5c.6 0 1.2 1.6 1.2 2.1 0 .6-.8.8-.6 1.4.4 1 1.2 1.8 2.2 2.2.6.2.8-.6 1.4-.6.5 0 2.1.6 2.1 1.2 0 .9-1 1.8-1.9 1.8C7.6 12.6 5.2 10.2 5.2 7.4c0-.9.9-2.9.8-2.9z" fill="var(--ink)"/>
      </svg>
      800.555.0148
    </p>
    <p class="contact-line contact-web">
      <svg width="18" height="18" viewBox="0 0 18 18" aria-hidden="true">
        <circle cx="9" cy="9" r="8" fill="none" stroke="var(--gold)" stroke-width="2"/>
        <ellipse cx="9" cy="9" rx="3.5" ry="8" fill="none" stroke="var(--gold)" stroke-width="1.5"/>
        <line x1="1" y1="9" x2="17" y2="9" stroke="var(--gold)" stroke-width="1.5"/>
      </svg>
      www.tidewelljourneys-example.com
    </p>
  </footer>

  <div class="brand">
    <span class="brand-dot"></span>
    <span>Tidewell Journeys</span>
  </div>
</main>
</body>
</html>
```